Pemberlux: Smart Quotes for Wine Lovers

Hello. I am completing book of quotes for wine lovers. Need the text formatted so that it is easy to read and aesthetically pleasing...modern, clean, smart. Number the pages. The cover is complete. Book is small square. 7.5 by 7.5 inches. If you want to show me first few pages that would be awesome. Thank you!
Updates

I edited the quotes so if you downloaded first ones, please grab these ones instead, thank you! 

Target Market(s)

wine lovers. Urban. Modern.

Industry/Entity Type

Quotes

Requirements
Should not have
• No color. black and white only.

```html
<!DOCTYPE html>
<html lang="en">
<head>
<meta charset="UTF-8">
<title>Pemberlux: Smart Quotes for Wine Lovers — Pages 38–39</title>
<link rel="stylesheet" href="https://fonts.googleapis.com/css2?family=EB+Garamond:wght@400&family=Lato:wght@400;700&display=swap">
<style>
  :root {
    --paper: #ffffff;
    --ink: #111111;
    --gutter: #cfcfcf;
  }
  * { margin: 0; padding: 0; box-sizing: border-box; }
  html, body {
    width: 1200px;
    height: 600px;
    overflow: hidden;
    background: var(--paper);
  }
  .spread {
    position: relative;
    width: 1200px;
    height: 600px;
    background: var(--paper);
    color: var(--ink);
  }
  .gutter {
    position: absolute;
    left: 601px;
    top: 0;
    width: 1px;
    height: 600px;
    background: var(--gutter);
  }
  .quote {
    position: absolute;
    top: 216px;
    font-family: "EB Garamond", Garamond, serif;
    font-size: 37px;
    line-height: 45.5px;
    font-weight: 400;
  }
  .quote--left { left: 95px; width: 320px; text-align: left; }
  .quote--right { right: 94px; width: 320px; text-align: right; }
  .attribution {
    display: block;
    margin-top: 10px;
    font-family: "Lato", Helvetica, sans-serif;
    font-size: 12.5px;
    line-height: 16px;
    letter-spacing: 0.12em;
    text-transform: uppercase;
  }
  .quote--right .attribution { margin-top: 7px; }
  .page-number {
    position: absolute;
    top: 523px;
    font-family: "Lato", Helvetica, sans-serif;
    font-size: 13px;
    line-height: 16px;
  }
  .page-number--left { left: 78px; }
  .page-number--right { right: 78px; }
  .footnote {
    position: absolute;
    top: 519px;
    width: 320px;
    font-family: "Lato", Helvetica, sans-serif;
    font-weight: 700;
    font-size: 7.4px;
    line-height: 10px;
  }
  .footnote--left { right: 648px; text-align: right; }
  .footnote--right { left: 663px; text-align: left; }
</style>
</head>
<body>
  <main class="spread">
    <section class="page page--verso">
      <blockquote class="quote quote--left">
        <p>The connoisseur<br>does not drink<br>wine but tastes its<br>secrets</p>
        <cite class="attribution">–Marcel Ardenne</cite>
      </blockquote>
      <span class="page-number page-number--left">38</span>
      <p class="footnote footnote--left">Marcel Étienne Ardenne de Valcourt, 1st Baron of Ardenne de<br>Valcourt (1902–1987) French Surrealist Painter.</p>
    </section>

    <div class="gutter"></div>

    <section class="page page--recto">
      <blockquote class="quote quote--right">
        <p>Wine is the<br>divine juice of<br>September.</p>
        <cite class="attribution">–Delacour</cite>
      </blockquote>
      <p class="footnote footnote--right">Jean-Luc Morvan&nbsp; known by his “nom de plume” Delacour.<br>(1696 –1779). French Enlightenment Writer, Historian and Philosopher.</p>
      <span class="page-number page-number--right">39</span>
    </section>
  </main>
</body>
</html>
```